Velundra Jobs portal

Velundra Jobs is a job portal connecting job seekers and companies offering part time jobs in the Mena region, starting in the UAE. We would like to see designs that use the color blue. We have attached images to give an idea what the website should look like. When a company posts a job the job seekers are not allowed to see which company has posted a job. There should also be a coinvex gateway. On the landing page we want a catching picture that we will send.

Target Market(s)

Students and promotional workers

Logo Text

Velundra Jobs

Coding

Coded - Design and coding required

Number of Pages Required

4 page

Font styles to use
Sans Serif

Colors
33a6d7
0692cd
85cae6

```html
<!DOCTYPE html>
<html lang="en">
<head>
<meta charset="utf-8">
<title>Velundra Jobs</title>
<link rel="stylesheet" href="https://fonts.googleapis.com/css2?family=Open+Sans:wght@400;600;700&display=swap">
<style>
  :root {
    --blue: #0692cd;
    --blue-mid: #33a6d7;
    --blue-light: #85cae6;
    --row-active: #70bbdc;
    --pink: #d6457e;
    --text-grey: #8a8a8a;
    --text-dark: #555;
    --line: #e6e6e6;
    --page-bg: #f5f5f5;
    --white: #fff;
  }
  * { box-sizing: border-box; margin: 0; padding: 0; }
  html, body { width: 1111px; height: 1200px; overflow: hidden; }
  body { font-family: "Open Sans", sans-serif; background: var(--page-bg); position: relative; color: var(--text-grey); }

  /* header */
  .site-header { position: absolute; top: 0; left: 0; width: 1111px; height: 87px; background: #f7f7f7; }
  .brand { position: absolute; left: 91px; top: 24px; display: flex; align-items: center; gap: 8px; }
  .brand-mark { width: 30px; height: 30px; border-radius: 50%; background: var(--blue-mid); }
  .brand-name { font-size: 27px; font-weight: 400; color: var(--blue-mid); letter-spacing: -0.5px; }
  .main-nav { position: absolute; left: 338px; top: 35px; display: flex; gap: 49px; font-size: 12px; color: #666; }
  .header-tools { position: absolute; right: 93px; top: 19px; display: flex; align-items: center; }
  .tool-search { width: 26px; height: 26px; margin-right: 14px; }
  .tool-bell { position: relative; width: 26px; height: 28px; margin-right: 24px; }
  .bell-count { position: absolute; left: 13px; top: 3px; width: 20px; height: 20px; border-radius: 50%; background: var(--blue-light); color: #fff; font-size: 10px; text-align: center; line-height: 20px; }
  .avatar { width: 50px; height: 50px; border-radius: 50%; background: radial-gradient(circle, #c79a80 30%, #b7454b 70%, #eee 72%); margin-right: 18px; }
  .btn-logout { width: 80px; height: 35px; background: var(--blue); border: 1px solid #0a7fb3; border-radius: 2px; color: #fff; font-size: 11px; display: flex; align-items: center; justify-content: center; gap: 6px; }

  /* hero */
  .hero { position: absolute; top: 87px; left: 0; width: 1111px; height: 241px; background: linear-gradient(180deg, #2a2f3d 0%, #3d3a48 45%, #5a3c3e 100%); }
  .hero h1 { position: absolute; top: 46px; width: 100%; text-align: center; font-size: 26px; font-weight: 700; color: #fff; letter-spacing: -0.3px; }
  .hero h2 { position: absolute; top: 88px; width: 100%; text-align: center; font-size: 19px; font-weight: 600; color: #eee; }
  .search-bar { position: absolute; left: 161px; top: 133px; width: 789px; height: 71px; background: rgba(200,200,200,0.45); border-radius: 3px; }
  .field { position: absolute; top: 10px; height: 47px; background: #fff; border-radius: 2px; font-size: 11.5px; color: #999; padding-left: 15px; line-height: 47px; }
  .field-type { left: 10px; width: 184px; }
  .field-loc { left: 202px; width: 184px; }
  .field-loc svg { position: absolute; right: 12px; top: 20px; }
  .field-lang { left: 396px; width: 232px; }
  .btn-filter { position: absolute; left: 638px; top: 10px; width: 138px; height: 48px; background: var(--pink); border: 1px solid #b83669; border-radius: 2px; color: #fff; font-size: 13px; font-weight: 600; display: flex; align-items: center; justify-content: center; gap: 8px; }

  /* categories */
  .categories { position: absolute; left: 91px; top: 372px; width: 216px; background: #fff; border: 1px solid var(--line); }
  .categories h3 { height: 38px; background: var(--blue-light); color: #fff; font-size: 15px; font-weight: 600; padding-left: 12px; line-height: 38px; margin: -1px -1px 0; }
  .cat-row { height: 35px; display: flex; justify-content: space-between; align-items: center; padding: 0 24px 0 16px; border-top: 1px solid #ececec; font-size: 12px; color: #999; }
  .cat-row:first-of-type { border-top: 0; }

  /* jobs table */
  .jobs { position: absolute; left: 335px; top: 372px; width: 684px; height: 425px; background: #fff; border: 1px solid var(--line); border-collapse: collapse; }
  .jobs th, .jobs td { border-left: 1px solid var(--line); border-top: 1px solid var(--line); text-align: center; font-size: 11.5px; color: #999; }
  .jobs tr > :first-child { border-left: 0; }
  .jobs th { height: 53px; color: var(--pink); font-weight: 600; font-size: 12px; }
  .jobs th.col-title { font-size: 15px; text-align: left; padding-left: 57px; }
  .jobs td.job-title { text-align: left; padding-left: 28px; font-size: 15px; font-weight: 600; color: #999; }
  .jobs tr.active td { background: var(--row-active); color: #fff; height: 57px; border-top-color: var(--row-active); }
  .jobs tr.active td.job-title { color: #fff; }
  .btn-apply { display: inline-block; width: 84px; height: 36px; line-height: 36px; background: var(--blue); color: #fff; font-size: 11px; font-weight: 600; border-radius: 2px; }
  .active .btn-apply { background: var(--pink); }

  /* featured */
  .featured { position: absolute; left: 0; top: 851px; width: 1111px; height: 290px; background: #fff; border-top: 1px solid #e2e2e2; }
  .featured h3 { position: absolute; left: 90px; top: 29px; font-size: 20px; font-weight: 600; color: var(--blue); }
  .slider-nav { position: absolute; right: 93px; top: 31px; display: flex; gap: 3px; }
  .slider-nav span { width: 27px; height: 27px; border-radius: 50%; border: 1px solid #ddd; display: flex; align-items: center; justify-content: center; }
  .provider { position: absolute; top: 79px; width: 174px; }
  .provider .photo { height: 118px; }
  .provider p { margin-top: 17px; font-size: 12px; color: #999; }
  .stars { margin-top: 6px; display: flex; gap: 2px; }

  /* footer */
  .site-footer { position: absolute; left: 0; top: 1141px; width: 1111px; height: 59px; background: var(--blue); color: #fff; font-size: 12px; }
  .copyright { position: absolute; left: 90px; top: 21px; }
  .social { position: absolute; left: 475px; top: 31px; display: flex; gap: 24px; }
  .social span { width: 14px; height: 14px; border-radius: 50%; background: #fff; opacity: 0.9; display: block; }
  .footer-links { position: absolute; right: 92px; top: 21px; }
</style>
</head>
<body>
  <header class="site-header">
    <div class="brand"><span class="brand-mark"></span><span class="brand-name">velundra</span></div>
    <nav class="main-nav"><span>ABOUT US</span><span>CONTACT US</span></nav>
    <div class="header-tools">
      <svg class="tool-search" viewBox="0 0 26 26"><circle cx="11" cy="11" r="8" fill="none" stroke="#777" stroke-width="3"/><line x1="17" y1="17" x2="24" y2="24" stroke="#777" stroke-width="3.5" stroke-linecap="round"/></svg>
      <div class="tool-bell">
        <svg width="22" height="26" viewBox="0 0 22 26"><path d="M11 3c-4 0-6 3-6 7v6l-3 4h18l-3-4v-6c0-4-2-7-6-7z" fill="none" stroke="#888" stroke-width="1.6"/><path d="M8 22a3 3 0 0 0 6 0" fill="none" stroke="#888" stroke-width="1.6"/></svg>
        <span class="bell-count">23</span>
      </div>
      <div class="avatar" role="img" aria-label="User profile photo"></div>
      <div class="btn-logout">
        <svg width="11" height="11" viewBox="0 0 12 12"><path d="M3.5 3a4.3 4.3 0 1 0 5 0" fill="none" stroke="#fff" stroke-width="1.6"/><line x1="6" y1="1" x2="6" y2="6" stroke="#fff" stroke-width="1.6"/></svg>
        LOGOUT
      </div>
    </div>
  </header>

  <section class="hero" role="img" aria-label="Night city skyline background">
    <h1>45,898 New jobs were Added last month!</h1>
    <h2>Start Your job search</h2>
    <div class="search-bar">
      <div class="field field-type">Types of work offered</div>
      <div class="field field-loc">Location<svg width="10" height="6" viewBox="0 0 10 6"><path d="M0 0h10L5 6z" fill="#888"/></svg></div>
      <div class="field field-lang">Languages spoken</div>
      <div class="btn-filter"><svg width="11" height="11" viewBox="0 0 12 12"><path d="M0 0h12L7 6v6L5 10V6z" fill="#fff"/></svg>FILTER SEARCH</div>
    </div>
  </section>

  <aside class="categories">
    <h3>OUR CATEGORIES</h3>
    <div class="cat-row"><span>Category 1</span><span style="color:#d6457e">(66)</span></div>
    <div class="cat-row"><span>Category 2</span><span style="color:#0692cd">(22)</span></div>
    <div class="cat-row"><span>Category 3</span><span style="color:#4cc4cf">(12)</span></div>
    <div class="cat-row"><span>Category 4</span><span style="color:#c0182c">(11)</span></div>
    <div class="cat-row"><span>Category 5</span><span style="color:#e6900f">(26)</span></div>
    <div class="cat-row"><span>Category 6</span><span style="color:#d82020">(342)</span></div>
    <div class="cat-row"><span>Category 7</span><span style="color:#1c6fb8">(633)</span></div>
    <div class="cat-row"><span>Category 8</span><span style="color:#33a6d7">(66)</span></div>
    <div class="cat-row"><span>Category 9</span><span style="color:#c0182c">(15)</span></div>
    <div class="cat-row"><span>Category 10</span><span style="color:#3a8a2a">(345)</span></div>
    <div class="cat-row"><span>Category 11</span><span style="color:#3a3aa8">(23)</span></div>
  </aside>

  <table class="jobs">
    <tr><th class="col-title" style="width:209px">Job Title</th><th style="width:206px">Due Date</th><th style="width:145px">Provider Name</th><th></th></tr>
    <tr class="active"><td class="job-title">Job Title number 1</td><td>Due Date: 23 jan 2015</td><td>Provider 1</td><td><span class="btn-apply">APPLY NOW</span></td></tr>
    <tr><td class="job-title">Job Title number 2</td><td>Due Date: 23 jan 2015</td><td>Provider 2</td><td><span class="btn-apply">APPLY NOW</span></td></tr>
    <tr><td class="job-title">Job Title number 3</td><td>Due Date: 23 jan 2015</td><td>Provider 3</td><td><span class="btn-apply">APPLY NOW</span></td></tr>
    <tr><td class="job-title">Job Title number 4</td><td>Due Date: 23 jan 2015</td><td>Provider 4</td><td><span class="btn-apply">APPLY NOW</span></td></tr>
    <tr><td class="job-title">Job Title number 5</td><td>Due Date: 23 jan 2015</td><td>Provider 5</td><td><span class="btn-apply">APPLY NOW</span></td></tr>
  </table>

  <section class="featured">
    <h3>Featured Job Providers</h3>
    <div class="slider-nav">
      <span><svg width="8" height="10" viewBox="0 0 8 10"><path d="M6 1L2 5l4 4" fill="none" stroke="#bbb" stroke-width="1.6"/></svg></span>
      <span><svg width="8" height="10" viewBox="0 0 8 10"><path d="M2 1l4 4-4 4" fill="none" stroke="#bbb" stroke-width="1.6"/></svg></span>
    </div>
    <div class="provider" style="left:91px"><div class="photo" role="img" aria-label="Doctor in a white coat" style="background:linear-gradient(135deg,#e4ecf2,#c9d6e0)"></div><p>Job Name: Loremi psm dolo</p><div class="stars">★★★★★</div></div>
    <div class="provider" style="left:281px"><div class="photo" role="img" aria-label="Engineer with hard hat and plans" style="background:linear-gradient(135deg,#cfe3ea,#8a9aa6)"></div><p>Job Name: Loremi psm dolo</p><div class="stars">★★★★★</div></div>
    <div class="provider" style="left:469px"><div class="photo" role="img" aria-label="Hand writing beside law books" style="background:linear-gradient(135deg,#7a2c22,#d8cbbb)"></div><p>Job Name: Loremi psm dolo</p><div class="stars">★★★★★</div></div>
    <div class="provider" style="left:657px"><div class="photo" role="img" aria-label="Team stacking hands together" style="background:linear-gradient(135deg,#9fb8d0,#d9cfc6)"></div><p>Job Name: Loremi psm dolo</p><div class="stars">★★★★★</div></div>
    <div class="provider" style="left:846px"><div class="photo" role="img" aria-label="Hand typing on a laptop" style="background:linear-gradient(135deg,#e6e6e6,#9a9a9a)"></div><p>Job Name: Loremi psm dolo</p><div class="stars">★★★★★</div></div>
  </section>

  <footer class="site-footer">
    <div class="copyright">Copyrights are reserved to Velundra 2015</div>
    <div class="social"><span></span><span></span><span></span><span></span><span></span></div>
    <div class="footer-links">About us &nbsp;-&nbsp; terms and conditions &nbsp;-&nbsp; Sitemap</div>
  </footer>
  <style>.stars { color: #ddd; font-size: 11px; letter-spacing: 0; }</style>
</body>
</html>
```